VENTURE CAPITAL GROUP BUSINESS CARD DESIGN

Venture Capital Group based in SF looking for a bold business card design. No trendy colour explosion, 3D effects etc. Just "simple" optical effects. Works on your brain, keeps your eye focused and sticks to your mind.
Target Market(s)
Technology startups
Industry/Entity Type
Venture Capital
Contact Information for Business Card
DESMOND WHITLAKE
MANAGING PARTNER
187 FENWORTH ST SAN FRANCISCO, CA 94187
415.555.0142 O
415.555.0147 F
415.555.0193 C
desmond@veldtmoorcapital.ventures

```html
<!DOCTYPE html>
<html lang="en">
<head>
<meta charset="utf-8">
<title>Veldtmoor Capital Group – Business Cards</title>
<link rel="stylesheet" href="https://fonts.googleapis.com/css2?family=Open+Sans:wght@400;600;700&display=swap">
<style>
  :root {
    --backdrop: #e6e6e4;
    --card-white: #ffffff;
    --brand-green: #1f8a34;
    --green-light: #4cb04c;
    --green-dark: #0b5e22;
    --band-grey: #d4d4d4;
    --band-grey-light: #ececec;
    --ink-white: #ffffff;
    --shadow: rgba(0, 0, 0, 0.18);
  }
  html, body {
    margin: 0;
    padding: 0;
    width: 1200px;
    height: 900px;
    overflow: hidden;
    background: var(--backdrop);
    font-family: "Open Sans", Arial, sans-serif;
  }
  .canvas {
    position: relative;
    width: 1200px;
    height: 900px;
  }
  .card {
    position: absolute;
    width: 560px;
    height: 320px;
    background: var(--card-white);
    box-shadow: 0 6px 18px var(--shadow);
    overflow: hidden;
  }
  /* Front card */
  .card-front { left: 540px; top: 90px; }
  .front-brand {
    position: absolute;
    inset: 0;
    display: flex;
    flex-direction: column;
    align-items: center;
    justify-content: center;
    gap: 18px;
  }
  .brand-dot {
    width: 92px;
    height: 92px;
    border-radius: 50%;
    background: radial-gradient(circle at 35% 30%, #ffffff 0%, var(--band-grey-light) 55%, var(--band-grey) 100%);
  }
  .brand-name {
    margin: 0;
    font-size: 26px;
    font-weight: 600;
    letter-spacing: 0.12em;
    color: var(--brand-green);
    text-transform: uppercase;
  }
  /* Back card */
  .card-back { left: 100px; top: 480px; }
  .back-art {
    position: absolute;
    inset: 0;
    width: 560px;
    height: 320px;
  }
  .back-brand {
    position: absolute;
    left: 22px;
    top: 84px;
    width: 150px;
    display: flex;
    flex-direction: column;
    align-items: center;
    gap: 12px;
  }
  .back-brand .brand-dot { width: 100px; height: 100px; }
  .back-brand .brand-name {
    font-size: 11px;
    letter-spacing: 0.08em;
    text-align: center;
    line-height: 1.5;
  }
  .contact {
    position: absolute;
    right: 24px;
    top: 56px;
    text-align: right;
    color: var(--ink-white);
  }
  .contact-name {
    margin: 0;
    font-size: 20px;
    font-weight: 700;
    line-height: 1.2;
  }
  .contact-title {
    margin: 2px 0 22px;
    font-size: 14px;
    font-weight: 400;
  }
  .contact-list {
    list-style: none;
    margin: 0;
    padding: 0;
    font-size: 13.5px;
    line-height: 1.55;
  }
  .contact-list li {
    display: flex;
    justify-content: flex-end;
    align-items: center;
    gap: 6px;
  }
  .contact-list svg {
    width: 12px;
    height: 12px;
    fill: var(--ink-white);
    flex: none;
  }
  .contact-list .address { padding-right: 18px; }
</style>
</head>
<body>
<main class="canvas">

  <section class="card card-front" aria-label="Card front">
    <div class="front-brand">
      <div class="brand-dot"></div>
      <p class="brand-name">Veldtmoor Capital Group</p>
    </div>
  </section>

  <section class="card card-back" aria-label="Card back">
    <svg class="back-art" viewBox="0 0 560 320" aria-hidden="true">
      <defs>
        <linearGradient id="greenFill" x1="0" y1="0" x2="0" y2="1">
          <stop offset="0" stop-color="#4cb04c"/>
          <stop offset="1" stop-color="#0b5e22"/>
        </linearGradient>
        <linearGradient id="greyBand" x1="0" y1="0" x2="1" y2="0">
          <stop offset="0" stop-color="#ececec"/>
          <stop offset="1" stop-color="#cfcfcf"/>
        </linearGradient>
      </defs>
      <path class="band-grey" d="M196 0 C262 80 252 230 138 320 L560 320 L560 0 Z" fill="url(#greyBand)"/>
      <path class="band-green" d="M214 0 C278 82 268 232 158 320 L560 320 L560 0 Z" fill="url(#greenFill)"/>
    </svg>

    <div class="back-brand">
      <div class="brand-dot"></div>
      <p class="brand-name">Veldtmoor Capital Group</p>
    </div>

    <div class="contact">
      <h1 class="contact-name">Desmond Whitlake</h1>
      <p class="contact-title">Managing Partner</p>
      <ul class="contact-list">
        <li>415.555.0142
          <svg viewBox="0 0 12 12"><path d="M2.4 1 4.2 2.8 3.4 4.2C4.1 5.7 5.9 7.5 7.6 8.4L8.9 7.6 11 9.4 10 11C5.6 10.6 1.4 6.4 1 2Z"/></svg>
        </li>
        <li>415.555.0147
          <svg viewBox="0 0 12 12"><path d="M3 1h5v3H3Z M1.5 4.5h9v6.5h-9Z" fill-opacity="0.95"/><rect x="3" y="6.5" width="1.5" height="1.2" fill="#0b5e22"/><rect x="5.3" y="6.5" width="1.5" height="1.2" fill="#0b5e22"/><rect x="7.6" y="6.5" width="1.5" height="1.2" fill="#0b5e22"/></svg>
        </li>
        <li>415.555.0193
          <svg viewBox="0 0 12 12"><path d="M3 0.5h6a1 1 0 0 1 1 1v9a1 1 0 0 1-1 1H3a1 1 0 0 1-1-1v-9a1 1 0 0 1 1-1Zm0.4 1.4v7.2h5.2V1.9Z"/></svg>
        </li>
        <li>desmond@veldtmoorcapital.ventures
          <svg viewBox="0 0 12 12"><path d="M0.5 2.5h11v7h-11Zm1 1 4.5 3.2 4.5-3.2" stroke="#0b5e22" stroke-width="0.8"/></svg>
        </li>
        <li class="address">187 Fenworth St San Francisco, CA 94187</li>
      </ul>
    </div>
  </section>

</main>
</body>
</html>
```